Personalised nutrition and health DNA report redesign

As part of our DNA report redesign, we are looking for new colour scheme that fits around our brand colours, more professional and slick design and more visual content/less text, but that conveys the same messages. We want it to be more visually appealing to customers and more user friendly and intuitive. We would like to it appeal to both males and females. It would be preferred for it to be done in Adobe InDesign and to receive the source file. I would need all pages redesigned. Thank you!
Target Market(s)
Mostly females, 30-55 but also some younger and middle aged men, professionals interested in their health
Industry/Entity Type
Health tech, Wellness
Look and feel
Each slider illustrates characteristics of the customer's brand and the style your logo design should communicate.

```html
<!DOCTYPE html>
<html lang="en">
<head>
<meta charset="utf-8">
<title>Genora Nutrition – DNA Report Pages</title>
<link href="https://fonts.googleapis.com/css2?family=Montserrat:wght@500;700;800&family=Roboto:wght@400;700&display=swap" rel="stylesheet">
<style>
:root{
  --stage:#262626;
  --ink:#141414;
  --blue:#1f6cff;
  --blue-deep:#0b3fd1;
  --blue-soft:#8eaaf8;
  --sky:#1a8cff;
  --magenta:#d11fe0;
  --orange:#f06a12;
  --lime:#7fcf1f;
  --green:#1fae48;
  --grey:#9a9a9a;
}
*{margin:0;padding:0;box-sizing:border-box}
html,body{width:1200px;height:498px;overflow:hidden;background:var(--stage)}
body{position:relative;font-family:"Roboto",Arial,sans-serif;color:var(--ink)}
.page{position:absolute;width:156px;height:221px;overflow:hidden;
  background:linear-gradient(180deg,#fff 0%,#fff 55%,var(--blue-soft) 100%)}
.row-1{top:19px}.row-2{top:256px}
.col-1{left:19px}.col-2{left:187px}.col-3{left:355px}.col-4{left:524px}
.col-5{left:691px}.col-6{left:858px}.col-7{left:1026px}
.abs{position:absolute}

/* header on inner pages */
.brand{position:absolute;left:13px;top:9px;font-family:"Montserrat",sans-serif;font-weight:800;
  font-size:7.4px;line-height:6.4px;color:var(--ink);letter-spacing:-.2px}
.tagline-bar{position:absolute;left:54px;right:0;top:12px;height:3.6px;background:var(--blue);
  color:#fff;font-family:"Montserrat",sans-serif;font-size:2.4px;letter-spacing:.5px;line-height:3.6px;padding-left:8px;white-space:nowrap;overflow:hidden}
.heading{position:absolute;left:13px;top:38px;font-family:"Montserrat",sans-serif;font-weight:700;font-size:3.4px}
.micro{font-size:2.2px;line-height:2.7px;color:#333}
.sub{font-family:"Montserrat",sans-serif;font-weight:700;font-size:2.6px;color:var(--blue)}

/* covers */
.cover{background:#fff}
.cover-photo{position:absolute;left:0;top:0;width:156px;height:150px}
.cover-swoosh{position:absolute;left:0;top:0}
.cover-brand{position:absolute;left:0;width:156px;top:124px;text-align:center;font-family:"Montserrat",sans-serif;
  font-weight:800;font-size:17px;line-height:16px;letter-spacing:-.5px}
.cover-band{position:absolute;left:0;width:156px;top:172px;height:3.8px;color:#fff;text-align:center;
  font-family:"Montserrat",sans-serif;font-size:2.4px;letter-spacing:.6px;line-height:3.8px;white-space:nowrap;overflow:hidden}
.cover-foot{position:absolute;left:0;top:175.8px;width:156px;bottom:0}
.cover-title{position:absolute;left:0;width:156px;top:192px;text-align:center;font-family:"Montserrat",sans-serif;
  font-weight:700;font-size:7.6px;color:var(--ink)}

/* letter */
.letter{position:absolute;left:13px;top:38px;width:130px}
.letter p{margin-bottom:2.2px;text-align:justify}

/* contents */
.toc{position:absolute;left:13px;top:49px;width:72px;list-style:none}
.toc li{display:flex;font-size:2.3px;line-height:3.05px;color:#333}
.toc li span:first-child{flex:1;border-bottom:.2px dotted #888;margin-right:1px}

/* glossary */
.pill{position:absolute;height:7px;border-radius:4px;background:var(--blue);color:#fff;font-family:"Montserrat",sans-serif;
  font-size:2.1px;line-height:2.5px;display:flex;align-items:center;justify-content:center;text-align:center}
.gloss-text{position:absolute;width:40px;text-align:justify}

/* sliders */
.slider-label{position:absolute;font-family:"Montserrat",sans-serif;font-weight:500;font-size:3.6px}
.bar{position:absolute;height:1.4px;background:var(--blue)}
.bar-light{background:#9fc0ff}
.marker{position:absolute;width:0;height:0;border-left:2px solid transparent;border-right:2px solid transparent;border-top:2.6px solid var(--blue-deep)}
.note{position:absolute;font-size:1.7px;line-height:2.1px;color:#333}

/* protein page */
.btn{position:absolute;height:7.5px;border-radius:4px;background:var(--blue);color:#fff;font-family:"Montserrat",sans-serif;
  font-size:2.1px;display:flex;align-items:center;justify-content:center;text-align:center;line-height:2.5px}
.col-text{position:absolute;text-align:justify}

/* back cover */
.back{background:#000}
.back-brand{position:absolute;left:0;width:156px;top:62px;text-align:center;font-family:"Montserrat",sans-serif;
  font-weight:800;font-size:15px;line-height:14px;color:var(--blue)}
.back-text{position:absolute;left:14px;top:105px;width:128px;font-size:1.8px;line-height:2.3px;color:#bbb}
</style>
</head>
<body>

<!-- Row 1 -->
<section class="page cover row-1 col-1">
  <div class="cover-photo" role="img" aria-label="Glowing blue DNA double helix on a dark background" style="background:radial-gradient(ellipse at 45% 35%,#3fa6ff 0%,#0a3aa8 35%,#020a2a 75%)"></div>
  <svg class="cover-swoosh" width="156" height="221" viewBox="0 0 156 221">
    <path d="M0,124 C60,96 110,84 156,50 L156,221 L0,221Z" fill="#8a8a8a"/>
    <path d="M0,130 C60,102 110,92 156,58 L156,221 L0,221Z" fill="var(--blue)"/>
    <path d="M0,143 C60,113 112,102 156,76 L156,221 L0,221Z" fill="#fff"/>
  </svg>
  <div class="cover-brand" style="color:var(--blue)">genora<br>nutrition</div>
  <div class="cover-band" style="background:var(--blue)">PERSONALISED NUTRITION FOR BETTER WELLBEING</div>
  <div class="cover-foot" style="background:linear-gradient(180deg,#f4f7ff,#d6e3ff)"></div>
  <div class="cover-title">SAMPLE DNA REPORT</div>
</section>

<section class="page row-1 col-2">
  <div class="brand">genora<br>nutrition</div>
  <div class="tagline-bar">PERSONALISED NUTRITION FOR BETTER WELLBEING</div>
  <div class="letter micro">
    <p>Hi (name)!</p>
    <p>Welcome to your DNA report. Here you will be able to find out about your genetic predispositions to a number of health outcomes like caffeine and salt sensitivity, your sugar and salt preference, optimal times to eat, your body fat response to protein, potential vitamin deficiencies and more! Outcomes we analysed are listed in the <b>table of contents</b> and are organised into different sections (weight management, taste preferences, cardiometabolic health, vitamin and mineral status, and food sensitivities). There is also a summary of your results first. But remember, there is much more information and advice for you throughout the report.</p>
    <p>For each outcome, you will be able to see the <b>gene and genetic variant</b> we have tested, <b>your result</b> and explanations on what this means for you. There is also a short <b>glossary</b> of basic terms and links to scientific articles if you would like to know more.</p>
    <p>Please bear in mind that when we talk about nutrigenetics, we are talking about probabilities. While our likelihood of having a specific condition may be increased if we have a specific genetic variant, this does not mean we will 100% have it. Our genes interact with the environment so our diet, lifestyle, exercise regime, all also play an important role.</p>
    <p>In your consultation, I will be explaining your report in detail, and we will agree on key goals that will help you take control of your health.</p>
    <p>I hope you enjoy your report and look forward to embarking with you on this journey to better nutrition!</p>
    <p>Dr. Mira Olsen</p>
  </div>
</section>

<section class="page row-1 col-3">
  <div class="brand">genora<br>nutrition</div>
  <div class="tagline-bar">PERSONALISED NUTRITION FOR BETTER WELLBEING</div>
  <div class="heading">TABLE OF CONTENTS:</div>
  <ul class="toc">
    <li><span>Glossary of Terms</span><span>4</span></li>
    <li><span>Summary of Your Results</span><span>5</span></li>
    <li><span>High Protein Diet</span><span>10</span></li>
    <li><span>Low Fat Diet</span><span>11</span></li>
    <li><span>Saturated Fat</span><span>12</span></li>
    <li><span>Meal Timing</span><span>13</span></li>
    <li><span>Physical Activity</span><span>14</span></li>
    <li><span>Cardio Training and Weight</span><span>15</span></li>
    <li><span>Exercise Motivation</span><span>16</span></li>
    <li><span>Sugar Preference</span><span>18</span></li>
    <li><span>Bitter Taster Status</span><span>19</span></li>
    <li><span>Salt Preference</span><span>20</span></li>
    <li><span>Salt Sensitivity</span><span>22</span></li>
    <li><span>Caffeine Sensitivity</span><span>23</span></li>
    <li><span>Omega-3</span><span>24</span></li>
    <li><span>Glucose Levels</span><span>25</span></li>
    <li><span>Glucose and Meal Timing</span><span>26</span></li>
    <li><span>Insulin Resistance</span><span>27</span></li>
    <li><span>Vitamin A</span><span>29</span></li>
    <li><span>Folate And Vitamin B2</span><span>30</span></li>
    <li><span>Vitamin B12</span><span>31</span></li>
    <li><span>Vitamin D</span><span>32</span></li>
    <li><span>Iron Overload</span><span>33</span></li>
    <li><span>Low Iron Status</span><span>34</span></li>
    <li><span>Choline</span><span>35</span></li>
    <li><span>Lactose Tolerance</span><span>37</span></li>
    <li><span>Gluten Sensitivity</span><span>38</span></li>
  </ul>
</section>

<section class="page row-1 col-4">
  <div class="brand">genora<br>nutrition</div>
  <div class="tagline-bar">PERSONALISED NUTRITION FOR BETTER WELLBEING</div>
  <div class="heading">GLOSSARY OF TERMS</div>
  <div class="pill" style="left:15px;top:50px;width:41px">DNA</div>
  <div class="pill" style="left:58px;top:50px;width:40px">GENE</div>
  <div class="pill" style="left:100px;top:50px;width:41px">GENETIC VARIANT</div>
  <p class="gloss-text micro" style="left:15px;top:59px">DNA or deoxyribonucleic acid is a long molecule that contains our unique genetic code. Like a recipe book it holds the instructions for making all the proteins in our bodies. It is built of four letters A, T, C and G.</p>
  <p class="gloss-text micro" style="left:58px;top:59px">A gene is a small section of DNA that contains the instructions for a specific molecule, usually a protein. For example, the FTO gene holds instructions to create a protein linked to fat mass and obesity. We all have this gene, but different people have different versions that make them respond differently.</p>
  <p class="gloss-text micro" style="left:100px;top:59px">Every human is unique, but if we were to look at our genes we would find that we are 99.9% the same. The 0.1% that differs is responsible for all the variation between us. Genetic variants are different versions of the same gene.</p>
  <div class="pill" style="left:15px;top:111px;width:41px">SINGLE NUCLEOTIDE POLYMORPHISM &amp; GENOTYPE</div>
  <div class="pill" style="left:58px;top:111px;width:40px">NUTRIGENETICS AND NUTRIGENOMICS</div>
  <div class="pill" style="left:100px;top:111px;width:41px">PERSONALISED NUTRITION</div>
  <p class="gloss-text micro" style="left:15px;top:120px">The most common form of genetic variants are single nucleotide polymorphisms, describing a change in a single letter in the DNA. They are identified by rs numbers you can see in your report. We inherit two copies of each gene, one from each parent, and together these are called genotypes.</p>
  <p class="gloss-text micro" style="left:58px;top:120px">Nutrigenetics explores how genetic variants affect the way we respond to different nutrients or types of exercise. Nutrigenomics, on the other hand, explores how the food we eat affects the way our genes are expressed.</p>
  <p class="gloss-text micro" style="left:100px;top:120px">It uses individual unique characteristics to tailor nutrition advice and optimise health. These can be a person's diet, food preferences, body composition, blood markers and DNA, among others.</p>
</section>

<section class="page row-1 col-5">
  <div class="brand">genora<br>nutrition</div>
  <div class="tagline-bar">PERSONALISED NUTRITION FOR BETTER WELLBEING</div>
  <div class="heading">SUMMARY OF YOUR RESULTS</div>
  <div class="sub abs" style="left:13px;top:48px;width:70px;line-height:3px">MACRONUTRIENT RATIO FOR<br>HEALTHY WEIGHT AND GLUCOSE LEVELS</div>
  <p class="micro abs" style="left:13px;top:57px;width:68px;font-size:1.8px;line-height:2.3px">• You are a high protein and low carb responder<br><br>• For healthy glucose levels, adhere to a dietary pattern such as the Mediterranean diet</p>
  <svg class="abs" style="left:85px;top:33px" width="58" height="58" viewBox="-29 -29 58 58" aria-label="Macronutrient pie chart">
    <circle r="28.5" fill="#cfe0ff"/>
    <path d="M0,0 L0,-27 A27,27 0 0 1 25.7,8.3 Z" fill="#1a7cff"/>
    <path d="M0,0 L25.7,8.3 A27,27 0 0 1 -25.7,8.3 Z" fill="#35a7f5"/>
    <path d="M0,0 L-25.7,8.3 A27,27 0 0 1 0,-27 Z" fill="#0a3bb8"/>
    <g fill="#fff" font-family="Montserrat,sans-serif" font-weight="700" font-size="2.4" text-anchor="middle">
      <text x="-11" y="-9">Protein</text><text x="-11" y="-6.3">25%</text>
      <text x="12" y="-3">Fat</text><text x="12" y="-0.3">35%</text>
      <text x="0" y="16">Carbohydrate</text><text x="0" y="18.7">40%</text>
    </g>
  </svg>
  <svg class="abs" style="left:13px;top:94px" width="20" height="14" viewBox="0 0 20 14" aria-label="Meal timing icon">
    <circle cx="10" cy="7" r="5.5" fill="none" stroke="var(--blue)" stroke-width="1.2"/>
    <path d="M10,4 V7 H12.5" fill="none" stroke="var(--blue)" stroke-width="1"/>
    <path d="M2,2 V12 M17.5,2 V12" stroke="var(--blue)" stroke-width="1.2"/>
  </svg>
  <div class="sub abs" style="left:13px;top:112px">MEAL TIMING</div>
  <p class="micro abs" style="left:13px;top:117px;width:130px;font-size:1.8px;line-height:2.4px">• Distribute your meals evenly throughout the day<br>• Avoid high carb meals for breakfast and opt for meals higher in protein for early breakfast and late dinner</p>
  <svg class="abs" style="left:13px;top:130px" width="14" height="14" viewBox="0 0 14 14" aria-label="Physical activity icon">
    <circle cx="9" cy="2.5" r="1.8" fill="var(--blue)"/>
    <path d="M8,5 L5,10 L2,12 M6.5,8 L10,10 L9.5,13.5 M8,5 L11,7.5 L13,6.5 M8,5 L4.5,5.5 L3,7.5" fill="none" stroke="var(--blue)" stroke-width="1.3" stroke-linecap="round"/>
  </svg>
  <div class="sub abs" style="left:13px;top:148px">PHYSICAL ACTIVITY</div>
  <p class="micro abs" style="left:13px;top:153px;width:130px;font-size:1.8px;line-height:2.4px">• Try and do more than 150 min of moderate/75 min of vigorous intensity per week<br>• Strength building exercises on 2 days a week (e.g. yoga, pilates, weight training, body weight moves)</p>
  <div class="sub abs" style="left:13px;top:170px;width:120px;font-weight:500;font-size:2.3px;line-height:2.9px">FOCUS ON CARDIO TRAINING IF TRYING TO LOSE OR MANAGE WEIGHT, AIM FOR FREQUENT AND SHORTER SESSIONS</div>
</section>

<section class="page row-1 col-6">
  <div class="brand">genora<br>nutrition</div>
  <div class="tagline-bar">PERSONALISED NUTRITION FOR BETTER WELLBEING</div>
  <div class="heading">SUMMARY OF YOUR RESULTS</div>
  <div class="sub abs" style="left:13px;top:48px;text-decoration:underline">VITAMIN AND MINERAL STATUS (LEGEND)</div>
  <div class="bar" style="left:15px;top:61px;width:64px"></div><div class="marker" style="left:15px;top:58px"></div>
  <div class="bar bar-light" style="left:15px;top:68px;width:64px;background:#4e8cff"></div><div class="marker" style="left:47px;top:65px"></div>
  <div class="bar bar-light" style="left:15px;top:75px;width:64px"></div><div class="marker" style="left:76px;top:72px"></div>
  <p class="note" style="left:86px;top:60px">No predisposition for low levels/ typical need</p>
  <p class="note" style="left:86px;top:67px">Medium predisposition for low levels/ moderately higher need</p>
  <p class="note" style="left:86px;top:74px">High predisposition for low levels/ higher need</p>
  <div class="slider-label" style="left:14px;top:92px">VITAMIN A</div><div class="bar" style="left:15px;top:101px;width:64px"></div><div class="marker" style="left:15px;top:98px"></div>
  <div class="slider-label" style="left:86px;top:92px">IRON</div><div class="bar bar-light" style="left:86px;top:101px;width:59px"></div><div class="marker" style="left:141px;top:98px"></div>
  <div class="slider-label" style="left:14px;top:114px">FOLATE AND VITAMIN B2</div><div class="bar" style="left:15px;top:122px;width:64px"></div><div class="marker" style="left:47px;top:119px"></div>
  <div class="slider-label" style="left:86px;top:114px">CHOLINE</div><div class="bar bar-light" style="left:86px;top:122px;width:59px"></div><div class="marker" style="left:141px;top:119px"></div>
  <div class="slider-label" style="left:14px;top:135px">VITAMIN B12</div><div class="bar" style="left:15px;top:143px;width:64px"></div><div class="marker" style="left:47px;top:140px"></div>
  <div class="slider-label" style="left:86px;top:135px">OMEGA-3</div><div class="bar bar-light" style="left:86px;top:143px;width:59px"></div><div class="marker" style="left:112px;top:140px"></div>
  <div class="slider-label" style="left:14px;top:158px">VITAMIN D</div><div class="bar bar-light" style="left:15px;top:166px;width:64px"></div><div class="marker" style="left:47px;top:163px"></div>
</section>

<section class="page row-1 col-7">
  <div class="brand">genora<br>nutrition</div>
  <div class="tagline-bar">PERSONALISED NUTRITION FOR BETTER WELLBEING</div>
  <div class="heading">SUMMARY OF YOUR RESULTS</div>
  <div class="sub abs" style="left:13px;top:48px;text-decoration:underline">TASTE PREFERENCES</div>
  <p class="micro abs" style="left:13px;top:55px;width:60px;font-size:1.8px;line-height:2.4px">• You likely have a "sweet tooth"<br>• You are a medium taster for bitter<br>• Your preference for salty foods is not high<br>• Be mindful of your intake of sweet foods<br>• Follow recommendations for salt intake based on your salt sensitivity genotype</p>
  <svg class="abs" style="left:96px;top:29px" width="44" height="56" viewBox="0 0 44 56" aria-label="Taste scale arrow from salty to sweet">
    <defs><linearGradient id="arrowFill" x1="0" y1="0" x2="0" y2="1"><stop offset="0" stop-color="#1f4fe0"/><stop offset="1" stop-color="#fff"/></linearGradient></defs>
    <path d="M22,1 L43,20 L32,20 L32,55 L12,55 L12,20 L1,20 Z" fill="url(#arrowFill)" stroke="#2a62ff" stroke-width=".6"/>
    <g font-family="Montserrat,sans-serif" font-size="2.4" text-anchor="middle" fill="#222">
      <text x="22" y="22">SWEET</text><text x="22" y="35">BITTER</text><text x="22" y="50">SALTY</text>
    </g>
    <path d="M22,24 V31 M22,37 V46" stroke="#444" stroke-width=".3"/>
  </svg>
  <div class="slider-label" style="left:13px;top:93px">SALT SENSITIVITY</div><div class="bar" style="left:14px;top:103px;width:64px"></div><div class="marker" style="left:75px;top:100px"></div>
  <p class="note" style="left:81px;top:102px">Blood pressure is sensitive to salt. Eat no more than 4 grams per day</p>
  <div class="slider-label" style="left:13px;top:114px">CAFFEINE SENSITIVITY</div><div class="bar bar-light" style="left:14px;top:123px;width:64px"></div><div class="marker" style="left:14px;top:120px"></div>
  <p class="note" style="left:81px;top:122px">You are a fast caffeine metaboliser<br>Your maximal caffeine intake = 400 mg (3-4 cups of coffee daily)</p>
  <div class="slider-label" style="left:13px;top:136px">LACTOSE INTOLERANCE</div><div class="bar bar-light" style="left:14px;top:145px;width:64px"></div><div class="marker" style="left:75px;top:142px"></div>
  <p class="note" style="left:81px;top:144px">You may be intolerant to lactose</p>
  <div class="slider-label" style="left:13px;top:157px">GLUTEN SENSITIVITY</div><div class="bar bar-light" style="left:14px;top:166px;width:64px"></div><div class="marker" style="left:14px;top:163px"></div>
  <p class="note" style="left:81px;top:165px">You are likely gluten tolerant</p>
</section>

<!-- Row 2 -->
<section class="page cover row-2 col-1">
  <div class="cover-photo" role="img" aria-label="Person measuring waist with a tape measure against a purple backdrop" style="background:linear-gradient(135deg,#caa2a0 0%,#7a4d8a 45%,#2a0f5e 100%)"></div>
  <svg class="cover-swoosh" width="156" height="221" viewBox="0 0 156 221">
    <path d="M0,124 C60,96 110,84 156,50 L156,221 L0,221Z" fill="#8a8a8a"/>
    <path d="M0,130 C60,102 110,92 156,58 L156,221 L0,221Z" fill="var(--magenta)"/>
    <path d="M0,143 C60,113 112,102 156,76 L156,221 L0,221Z" fill="#fbf2ff"/>
  </svg>
  <div class="cover-brand" style="color:var(--magenta)">genora<br>nutrition</div>
  <div class="cover-band" style="background:var(--magenta)">PERSONALISED NUTRITION FOR BETTER WELLBEING</div>
  <div class="cover-foot" style="background:linear-gradient(180deg,#f6ecff,#d8b3f5)"></div>
  <div class="cover-title">WEIGHT MANAGEMENT</div>
</section>

<section class="page cover row-2 col-2">
  <div class="cover-photo" role="img" aria-label="Blue x-ray style human body illustration with DNA strand" style="background:radial-gradient(ellipse at 50% 40%,#6cc8ff 0%,#1a72e0 45%,#0a3aa0 100%)"></div>
  <svg class="cover-swoosh" width="156" height="221" viewBox="0 0 156 221">
    <path d="M0,124 C60,96 110,84 156,50 L156,221 L0,221Z" fill="#8a8a8a"/>
    <path d="M0,130 C60,102 110,92 156,58 L156,221 L0,221Z" fill="#0a2a8a"/>
    <path d="M0,143 C60,113 112,102 156,76 L156,221 L0,221Z" fill="#f2f7ff"/>
  </svg>
  <div class="cover-brand" style="color:var(--sky)">genora<br>nutrition</div>
  <div class="cover-band" style="background:var(--sky)">PERSONALISED NUTRITION FOR BETTER WELLBEING</div>
  <div class="cover-foot" style="background:linear-gradient(180deg,#e8f2ff,#9cc6ff)"></div>
  <div class="cover-title">TASTE PREFERENCES</div>
</section>

<section class="page cover row-2 col-3">
  <div class="cover-photo" role="img" aria-label="Woman running with a glowing orange DNA helix" style="background:linear-gradient(120deg,#6b4a2a 0%,#e8801c 45%,#ffb21c 70%,#d24a0a 100%)"></div>
  <svg class="cover-swoosh" width="156" height="221" viewBox="0 0 156 221">
    <path d="M0,124 C60,96 110,84 156,50 L156,221 L0,221Z" fill="#8a8a8a"/>
    <path d="M0,130 C60,102 110,92 156,58 L156,221 L0,221Z" fill="var(--orange)"/>
    <path d="M0,143 C60,113 112,102 156,76 L156,221 L0,221Z" fill="#fff8ef"/>
  </svg>
  <div class="cover-brand" style="color:var(--orange)">genora<br>nutrition</div>
  <div class="cover-band" style="background:var(--orange)">PERSONALISED NUTRITION FOR BETTER WELLBEING</div>
  <div class="cover-foot" style="background:linear-gradient(180deg,#fff1e2,#ffcf95)"></div>
  <div class="cover-title">CARDIOMETABOLIC HEALTH</div>
</section>

<section class="page cover row-2 col-4">
  <div class="cover-photo" role="img" aria-label="Vitamin capsules and pills with a golden DNA helix" style="background:linear-gradient(120deg,#e8e2c8 0%,#c9c04a 40%,#f0c020 65%,#7a8a20 100%)"></div>
  <svg class="cover-swoosh" width="156" height="221" viewBox="0 0 156 221">
    <path d="M0,124 C60,96 110,84 156,50 L156,221 L0,221Z" fill="#8a8a8a"/>
    <path d="M0,130 C60,102 110,92 156,58 L156,221 L0,221Z" fill="var(--lime)"/>
    <path d="M0,143 C60,113 112,102 156,76 L156,221 L0,221Z" fill="#f8ffee"/>
  </svg>
  <div class="cover-brand" style="color:var(--lime)">genora<br>nutrition</div>
  <div class="cover-band" style="background:var(--lime)">PERSONALISED NUTRITION FOR BETTER WELLBEING</div>
  <div class="cover-foot" style="background:linear-gradient(180deg,#f1fbe2,#c9ef8e)"></div>
  <div class="cover-title">VITAMIN AND MINERAL STATUS</div>
</section>

<section class="page cover row-2 col-5">
  <div class="cover-photo" role="img" aria-label="Fresh salad with prawns and vegetables" style="background:radial-gradient(ellipse at 55% 45%,#e8b690 0%,#8aa848 40%,#2e6a20 80%)"></div>
  <svg class="cover-swoosh" width="156" height="221" viewBox="0 0 156 221">
    <path d="M0,124 C60,96 110,84 156,50 L156,221 L0,221Z" fill="#8a8a8a"/>
    <path d="M0,130 C60,102 110,92 156,58 L156,221 L0,221Z" fill="var(--green)"/>
    <path d="M0,143 C60,113 112,102 156,76 L156,221 L0,221Z" fill="#f0fff4"/>
  </svg>
  <div class="cover-brand" style="color:var(--green)">genora<br>nutrition</div>
  <div class="cover-band" style="background:var(--green)">PERSONALISED NUTRITION FOR BETTER WELLBEING</div>
  <div class="cover-foot" style="background:linear-gradient(180deg,#e6faeb,#9ee6ac)"></div>
  <div class="cover-title">FOOD SENSITIVITIES</div>
</section>

<section class="page row-2 col-6">
  <div class="brand">genora<br>nutrition</div>
  <div class="tagline-bar">PERSONALISED NUTRITION FOR BETTER WELLBEING</div>
  <div class="heading">HIGH PROTEIN DIET</div>
  <div class="col-text micro" style="left:13px;top:47px;width:62px;font-size:1.9px;line-height:2.4px">
    <p style="margin-bottom:2px">Protein is a key nutrient that helps build and repair our body. It also keeps us feeling full and supports our immune system.</p>
    <p style="margin-bottom:2px">You can get protein from foods like chicken, fish, low-fat dairy, beans, lentils, and eggs. For weight loss, protein can be especially helpful.</p>
    <p style="margin-bottom:2px">Some research suggests that if you have a certain version of the FTO gene, known as the "obesity gene", eating more protein might help you lose weight more effectively.</p>
    <p>The FTO gene can affect our weight and how our body stores fat. Interestingly, it might also influence our brain in ways that impact our food choices and self-control. So, for some, a protein-rich diet could be a good strategy for weight loss.</p>
  </div>
  <div class="abs" role="img" aria-label="Roast chicken on a plate" style="left:92px;top:26px;width:42px;height:40px;border-radius:50%;background:radial-gradient(circle at 50% 45%,#c8782a 0%,#8a4a1a 55%,#e9e4dc 72%,#fff 80%)"></div>
  <div class="btn" style="left:97px;top:72px;width:27px">GENE - FTO</div>
  <div class="sub abs" style="left:80px;top:83px;width:66px;text-align:center;font-size:2.3px">GENETIC VARIANT (VERSIONS)</div>
  <div class="abs" style="left:80px;top:86px;width:66px;text-align:center;font-size:2.3px;line-height:2.8px">RS1558902 (A/T)<br>RS9939609 (A/T)</div>
  <div class="sub abs" style="left:80px;top:98px;width:66px;text-align:center;font-size:2.3px">YOUR VERSION</div>
  <div class="abs" style="left:80px;top:101px;width:66px;text-align:center;font-size:2.3px">AA/AT</div>
  <div class="btn" style="left:12px;top:115px;width:63px">WHAT DOES IT MEAN FOR YOU</div>
  <div class="btn" style="left:81px;top:115px;width:64px">CLICK LINKS BELOW FOR<br>SCIENTIFIC ARTICLES ON THIS TOPIC</div>
  <p class="col-text micro" style="left:13px;top:128px;width:62px;font-size:1.9px;line-height:2.4px">You have AA/AT, combination of the FTO gene which means you have an elevated weight loss response to a high protein diet. You may also lose more fat mass while on a high protein diet. If you are trying to lose weight or fat mass, consume approximately 25% of energy from protein as part of a balanced diet. For a 1500 calorie diet, this would be approximately 90 grams of protein per day. If you need to increase your protein intake, replace some carbohydrate rich meals with meals higher in protein. Opt for a higher protein breakfast such as plain yoghurt or eggs. Snack on nuts and seeds but be mindful that one portion is one small handful. Include beans and pulses and lean meat for your lunch or dinner. Add a source of protein to your salad (e.g. canned sardines or tuna).</p>
  <div class="col-text micro" style="left:82px;top:128px;width:63px;font-size:1.9px;line-height:2.4px">
    <p style="margin-bottom:2px">FTO Genotype and 2-Year Change in Body Composition and Fat Distribution in Response to Weight-Loss Diets: The Lost Pounds Trial</p>
    <p style="margin-bottom:2px">FTO genotype, dietary protein intake, and body weight in a multiethnic population of young adults: a cross-sectional study</p>
    <p style="margin-bottom:2px">Assessment of the FTO gene polymorphisms (rs1421085, rs17817449 and rs9939609) in exercise-trained men and women: the effects of a 4-week hypocaloric diet</p>
    <p>Effects of a High-Protein/Low-Carbohydrate Diet versus a Standard Hypocaloric Diet on Weight and Cardiovascular Risk Factors: Role of a Genetic Variation in the rs9939609 FTO Gene Variant</p>
  </div>
</section>

<section class="page back row-2 col-7">
  <div class="back-brand">genora<br>nutrition</div>
  <p class="back-text">Genora Nutrition is not a medical care provider and the advice is intended to be informational or educational. The Report is not a substitute for, or an alternative to, any other medical or therapeutic services or treatments that are available or for any medication prescribed to you. Unless otherwise stated within the Report, the Report is not intended to diagnose, treat or cure any illness or disease or provide information on disease risk. Genetic testing and any other science used to input into a Report, and the associated results, are always improving and changing as technology and understanding develops. Accordingly, the recommendations of a Report may not remain current. If you have any questions about the Report, please contact us at hello@genoranutrition.example</p>
</section>

</body>
</html>
```